Business Card, A4 Letter Head and DL Envelope for Brandvelle

We are looking for a design for our Business Card, A4 Letter Head and DL Envelope.

Brandvelle is a distributor of promotional products. We specialize in a range of branded promotional products, these include pens, polo shirts, key rings, drink bottles, uniforms and bags to name a few. We are experts in marketing and assist companies in choosing the right promotional product for their needs. We will predominately be an online business where customers visit our website and browse our range of promotional products and branding options.

Our colours are black, red, white and grey.

Files must be supplied in eps, pdf and ai format.

Please display the following information:
Derek Halloway
Account Manager
Suite xxx, 212 Ferrow Lane Melbourne, Victoria 3000
Phone +61 3 5550 1827
Mobile +61 455 016 342
sales@brandvelle-example.com.au
www.brandvelle-example.com.au

```html
<!DOCTYPE html>
<html lang="en">
<head>
<meta charset="utf-8">
<title>Brandvelle Business Card</title>
<link rel="stylesheet" href="https://fonts.googleapis.com/css2?family=Open+Sans:wght@400;600;700;800&display=swap">
<style>
  :root {
    --page-bg: #e9e6e1;
    --card-white: #ffffff;
    --brand-red: #d4141c;
    --brand-red-dark: #8c0d12;
    --brand-red-deep: #6e0a0e;
    --charcoal: #3a3b3e;
    --text-grey: #5b5c60;
  }
  * { margin: 0; padding: 0; box-sizing: border-box; }
  html, body {
    width: 1200px; height: 1024px; overflow: hidden;
    background: var(--page-bg);
    font-family: "Open Sans", Arial, sans-serif;
  }
  .canvas {
    width: 1200px; height: 1024px;
    display: flex; flex-direction: column; align-items: center;
    justify-content: center; gap: 24px;
  }
  .card {
    position: relative; width: 840px; height: 480px;
    border-radius: 28px; overflow: hidden;
    box-shadow: 0 10px 28px rgba(0,0,0,0.22);
  }
  /* Front */
  .card-front { background: var(--card-white); }
  .card-front .swoosh { position: absolute; inset: 0; }
  .brand-lockup {
    position: absolute; left: 60px; top: 300px;
    display: flex; align-items: center; gap: 18px;
  }
  .brand-dot {
    width: 46px; height: 46px; border-radius: 50%;
    background: var(--brand-red);
  }
  .brand-name {
    font-weight: 800; font-size: 46px; letter-spacing: 1px;
    color: var(--charcoal); text-transform: uppercase;
  }
  .contact {
    position: absolute; left: 400px; top: 40px; color: var(--text-grey);
    display: flex; flex-direction: column;
  }
  .contact-name {
    font-weight: 700; font-size: 24px; color: var(--brand-red);
    text-transform: uppercase; letter-spacing: 0.5px;
  }
  .contact-title { font-size: 18px; margin-bottom: 10px; }
  .contact-line {
    display: flex; align-items: center; gap: 8px;
    font-size: 15px; line-height: 24px;
  }
  .contact-line svg { width: 14px; height: 14px; flex: none; }
  .divider {
    width: 240px; height: 2px; margin: 14px 0 12px -40px;
    background: linear-gradient(90deg, transparent, var(--brand-red) 50%, transparent);
  }
  .contact-address { font-size: 15px; line-height: 22px; }
  .front-web {
    position: absolute; right: 44px; bottom: 30px;
    color: #fff; font-size: 17px; letter-spacing: 0.3px;
  }
  /* Back */
  .card-back {
    background: radial-gradient(ellipse at 55% 45%, var(--brand-red) 0%, var(--brand-red-dark) 70%, var(--brand-red-deep) 100%);
    display: flex; flex-direction: column; align-items: center; justify-content: center;
  }
  .back-lockup { display: flex; align-items: center; gap: 22px; }
  .back-lockup .brand-dot { width: 58px; height: 58px; background: #ffffff; }
  .back-lockup .brand-name { color: #ffffff; font-size: 60px; }
  .back-web { margin-top: 22px; color: #fff; font-size: 19px; letter-spacing: 0.4px; }
</style>
</head>
<body>
<main class="canvas">
  <section class="card card-front" aria-label="Business card front">
    <svg class="swoosh" viewBox="0 0 840 480" preserveAspectRatio="none" aria-hidden="true">
      <defs>
        <linearGradient id="bandRed" x1="0" y1="1" x2="1" y2="0">
          <stop offset="0" stop-color="#8c0d12"/>
          <stop offset="0.5" stop-color="#e01a22"/>
          <stop offset="1" stop-color="#9e0f15"/>
        </linearGradient>
        <linearGradient id="bandSteel" x1="0" y1="1" x2="1" y2="0">
          <stop offset="0" stop-color="#6f7074"/>
          <stop offset="0.5" stop-color="#e6e7e9"/>
          <stop offset="1" stop-color="#8d8f93"/>
        </linearGradient>
      </defs>
      <path d="M260 480 C540 430 740 310 806 0 L840 0 L840 480 Z" fill="#2b2c2f"/>
      <path d="M285 480 C560 428 755 310 816 0 L840 0 L840 480 Z" fill="url(#bandSteel)"/>
      <path d="M320 480 C585 425 770 312 830 0 L840 0 L840 480 Z" fill="url(#bandRed)"/>
    </svg>
    <div class="brand-lockup">
      <span class="brand-dot"></span>
      <span class="brand-name">Brandvelle</span>
    </div>
    <div class="contact">
      <div class="contact-name">Derek Halloway</div>
      <div class="contact-title">Account Manager</div>
      <div class="contact-line">
        <svg viewBox="0 0 14 14"><path d="M3 1l2.5 2.5-1.5 2a8 8 0 0 0 4.5 4.5l2-1.5L13 11l-2 2C6 13 1 8 1 3z" fill="#d4141c"/></svg>
        +61 3 5550 1827
      </div>
      <div class="contact-line">
        <svg viewBox="0 0 14 14"><rect x="3.5" y="1" width="7" height="12" rx="1.2" fill="none" stroke="#5b5c60" stroke-width="1.4"/><circle cx="7" cy="11" r="0.8" fill="#5b5c60"/></svg>
        +61 455 016 342
      </div>
      <div class="contact-line">
        <svg viewBox="0 0 14 14"><rect x="1" y="2.5" width="12" height="9" rx="1" fill="#d4141c"/><path d="M1.5 3.5L7 8l5.5-4.5" fill="none" stroke="#fff" stroke-width="1.2"/></svg>
        sales@brandvelle-example.com.au
      </div>
      <div class="divider"></div>
      <div class="contact-address">Suite xxx, 212 Ferrow Lane<br>Melbourne, Victoria 3000</div>
    </div>
    <div class="front-web">www.brandvelle-example.com.au</div>
  </section>

  <section class="card card-back" aria-label="Business card back">
    <div class="back-lockup">
      <span class="brand-dot"></span>
      <span class="brand-name">Brandvelle</span>
    </div>
    <div class="back-web">www.brandvelle-example.com.au</div>
  </section>
</main>
</body>
</html>
```